Venture 482 - Lumora Book Cover

I am looking for a Lumora book cover for my book about "Venture 482".
The Book is Titled:
Venture 482 Ascended
Shaping Outcomes: Paths To Unlocking Cosmic Truths
Author is Dorian Pell
Here is a book description that may help you understand more about it:
Inspired by the genius of Edwin Marlowe, this comprehensive guide delves into the ancient wisdom and cutting-edge science behind the 482 method, a powerful tool for manifesting your desires. Whether you're seeking personal growth, financial success, or spiritual enlightenment, this book provides advanced techniques and methods to transform your dreams into reality.
Any questions please ask.
Thanks
Owen

```html
<!DOCTYPE html>
<html lang="en">
<head>
<meta charset="utf-8">
<title>Venture 482 Ascended — Dorian Pell</title>
<link rel="stylesheet" href="https://fonts.googleapis.com/css2?family=Cinzel:wght@400;500&family=Cormorant+Garamond:wght@500&family=Tinos&display=swap">
<style>
  :root {
    --ink-cream: #f8e6d8;
    --night: #140a22;
    --violet: #5b2f7c;
    --orchid: #a45fb8;
    --glow: #f3d6b0;
    --ember: #c8641e;
  }
  html, body {
    margin: 0;
    padding: 0;
    width: 805px;
    height: 1200px;
    overflow: hidden;
    background: var(--night);
  }
  .cover {
    position: relative;
    width: 805px;
    height: 1200px;
    overflow: hidden;
    color: var(--ink-cream);
    text-align: center;
  }
  .cover-art {
    position: absolute;
    inset: 0;
    background:
      radial-gradient(ellipse 120px 200px at 402px 470px, rgba(243,214,176,0.55), transparent 70%),
      radial-gradient(circle 330px at 402px 520px, rgba(164,95,184,0.55), rgba(91,47,124,0.35) 65%, transparent 100%),
      radial-gradient(ellipse 420px 180px at 402px 1120px, rgba(200,100,30,0.45), transparent 70%),
      radial-gradient(ellipse 300px 300px at 60px 200px, rgba(150,60,70,0.25), transparent 70%),
      radial-gradient(ellipse 300px 300px at 760px 250px, rgba(150,60,70,0.25), transparent 70%),
      linear-gradient(180deg, #1d0e2c 0%, #2a1238 45%, #1a0c24 80%, #120818 100%);
  }
  .title {
    position: absolute;
    left: 0;
    right: 0;
    margin: 0;
    font-weight: 400;
  }
  .title-word {
    top: 262px;
    font-family: "Cinzel", serif;
    font-size: 150px;
    line-height: 1;
    letter-spacing: -0.01em;
    text-transform: none;
  }
  .title-word .initial { font-size: 150px; }
  .title-word .rest { font-size: 118px; text-transform: uppercase; }
  .title-number {
    top: 385px;
    font-family: "Cormorant Garamond", serif;
    font-weight: 500;
    font-size: 390px;
    line-height: 1;
    letter-spacing: -0.04em;
    font-variant-numeric: oldstyle-nums;
    font-feature-settings: "onum" 1;
  }
  .title-tier {
    top: 798px;
    font-family: "Cinzel", serif;
    font-size: 74px;
    line-height: 1;
    letter-spacing: 0.24em;
    padding-left: 0.24em;
  }
  .subtitle {
    position: absolute;
    left: 0;
    right: 0;
    top: 902px;
    font-family: "Tinos", serif;
  }
  .subtitle-lead {
    margin: 0 0 14px;
    font-size: 31px;
    line-height: 1.1;
    text-transform: uppercase;
  }
  .subtitle-line {
    margin: 0;
    font-size: 28px;
    line-height: 1.2;
  }
  .author {
    position: absolute;
    left: 0;
    right: 0;
    top: 1082px;
    margin: 0;
    font-family: "Cinzel", serif;
    font-weight: 400;
    font-size: 58px;
    line-height: 1;
    letter-spacing: 0.22em;
    padding-left: 0.22em;
  }
</style>
</head>
<body>
  <main class="cover">
    <div class="cover-art" role="img" aria-label="Cosmic purple scene with a silhouetted figure meditating cross-legged before a glowing geometric mandala, a beam of light descending from above and warm amber light beneath"></div>

    <h1 class="title title-word"><span class="initial">V</span><span class="rest">enture</span></h1>
    <p class="title title-number">482</p>
    <p class="title title-tier">ASCENDED</p>

    <div class="subtitle">
      <p class="subtitle-lead">Shaping Outcomes:</p>
      <p class="subtitle-line">Paths to unlocking</p>
      <p class="subtitle-line">cosmic truths</p>
    </div>

    <p class="author">DORIAN PELL</p>
  </main>
</body>
</html>
```